Custom unique Stationary design for Logistics company

We need a custom, unique , elegant and luxurious full stationary design using our new logo, following these guidelines:
1- Business card: double sided, both sides uses the navy blue as the background main color (same as the code of the navy blue used in our logo).
2- envelope and folder: also use the same navy blue as the main background color.
3- book cover( notepad cover) : same thing with the navy blue
4- letterhead: feel free to use the combination of the colors in our logo.
5- rest of the items are up to your creativity

Target Market(s)

corporates and other businesses

Industry/Entity Type

Logistics and heavy machines contractors

Requirements
Must have
• Letterhead, business card, envelope, notepad cover, paper, file
Nice to have
• navy blue to be main background color for business card, envelope, notepad cover

```html
<!DOCTYPE html>
<html lang="en">
<head>
<meta charset="utf-8">
<title>Northbound Freight Group — Business Card</title>
<link rel="stylesheet" href="https://fonts.googleapis.com/css2?family=Montserrat:wght@600;800&family=Arimo:wght@400&display=swap">
<style>
  :root {
    --backdrop: #e4e4e4;
    --navy: #0b4670;
    --navy-deep: #063b60;
    --orange: #f0582a;
    --white: #ffffff;
  }
  * { box-sizing: border-box; margin: 0; padding: 0; }
  html, body {
    width: 1200px; height: 800px; overflow: hidden;
    background: var(--backdrop);
  }
  .sheet {
    width: 1200px; height: 800px;
    display: flex; align-items: center; justify-content: center; gap: 40px;
  }
  .card {
    position: relative;
    width: 540px; height: 309px;
    border-radius: 22px;
    background: linear-gradient(160deg, var(--navy) 0%, var(--navy-deep) 100%);
    box-shadow: 0 0 0 2px var(--orange);
    overflow: hidden;
  }
  /* Contact side */
  .identity {
    position: absolute; right: 268px; top: 128px;
    text-align: right;
  }
  .identity__name {
    font-family: "Montserrat", sans-serif; font-weight: 800;
    font-size: 24px; letter-spacing: 0.5px; color: var(--orange);
    line-height: 1;
  }
  .identity__role {
    font-family: "Montserrat", sans-serif; font-weight: 800;
    font-size: 15px; color: var(--white); margin-top: 4px;
  }
  .divider {
    position: absolute; left: 290px; top: 92px;
    width: 1.5px; height: 126px; background: var(--orange);
  }
  .contacts {
    position: absolute; left: 308px; top: 96px;
    list-style: none;
    font-family: "Arimo", sans-serif; font-size: 11.5px;
    color: var(--white); line-height: 1.35;
  }
  .contacts li { display: flex; align-items: flex-start; gap: 8px; margin-bottom: 3px; }
  .contacts svg { width: 11px; height: 11px; flex: none; margin-top: 2px; }
  .contacts .group { margin-bottom: 8px; }
  /* Brand side */
  .brand {
    position: absolute; inset: 0;
    display: flex; align-items: center; justify-content: center; gap: 12px;
  }
  .brand__dot {
    width: 18px; height: 18px; border-radius: 50%; background: var(--orange);
  }
  .brand__name {
    font-family: "Montserrat", sans-serif; font-weight: 800;
    font-size: 24px; letter-spacing: 1px; color: var(--white);
  }
</style>
</head>
<body>
<main class="sheet">
  <section class="card card--contact">
    <div class="identity">
      <p class="identity__name">DANIEL HARPER</p>
      <p class="identity__role">President</p>
    </div>
    <div class="divider"></div>
    <ul class="contacts">
      <li class="group">
        <svg viewBox="0 0 12 12"><path d="M6 0.5a4 4 0 0 1 4 4c0 3-4 7-4 7s-4-4-4-7a4 4 0 0 1 4-4z" fill="var(--orange)"/><circle cx="6" cy="4.5" r="1.5" fill="var(--navy)"/></svg>
        <span>4120 Birchwood Drive<br>Fairbanks, Alaska 99701</span>
      </li>
      <li>
        <svg viewBox="0 0 12 12"><path d="M2 1h2.5l1 3-1.5 1a7 7 0 0 0 3 3l1-1.5 3 1V10a1 1 0 0 1-1 1A9 9 0 0 1 1 2a1 1 0 0 1 1-1z" fill="var(--orange)"/></svg>
        <span>555-214-7730</span>
      </li>
      <li>
        <svg viewBox="0 0 12 12"><rect x="3" y="0.5" width="6" height="11" rx="1" fill="none" stroke="var(--white)" stroke-width="1.2"/></svg>
        <span>555-468-2091</span>
      </li>
      <li>
        <svg viewBox="0 0 12 12"><rect x="0.5" y="2" width="11" height="8" fill="var(--orange)"/><path d="M0.5 2l5.5 4.5L11.5 2" fill="none" stroke="var(--navy)" stroke-width="1"/></svg>
        <span>info@northboundfreight.com</span>
      </li>
      <li>
        <svg viewBox="0 0 12 12"><circle cx="6" cy="6" r="5.5" fill="var(--orange)"/><path d="M0.5 6h11M6 0.5c-3 3-3 8 0 11M6 0.5c3 3 3 8 0 11" fill="none" stroke="var(--navy)" stroke-width="0.8"/></svg>
        <span>northboundfreight.com</span>
      </li>
    </ul>
  </section>

  <section class="card card--brand">
    <div class="brand">
      <span class="brand__dot"></span>
      <span class="brand__name">NORTHBOUND FREIGHT GROUP</span>
    </div>
  </section>
</main>
</body>
</html>
```